Web Design Project

Crest Tide needs a new web page design.

This final product MUST be a layered .psd format for our CSS coder to do properly.

What we need is a 3 column template similar to the attached sample. We NEED to have 3 defined sections "Learn" "Shop" and "Dive." This is very important.

Our store font is Ethnocentric, so any design which incorporates this somehow would be great. Our logo is attached in a .jpeg and .psd format. Feel free to manipulate the logo background into a design that works.

Preferred colors are blue (not light blue,) grey, black and yellow. The center section of the template must remain white.

Crest Tide is a website for technical and rebreather equipment, and training. PLEASE do NOT show images of recreational scuba divers. This is not our market and designs featuring recreational 'touristy' divers will be eliminated.

Attached are logos, and images for use as a background image.

Target Market(s)

Males 25-60

Industry/Entity Type

Store

Requirements
Must have
• - 3 defined sections "Learn" "Shop" "Dive"
- White center area
- Final format must be delivered in a layered .psd file for our CSS coder to cut
Nice to have
• -Ethnocentric fonts
-3d borders
-Textures
- Blue, great black, yellow colors.
- Simple, uncluttered design
Should not have
• Images or logos of recreational or 'tourist' scuba divers. This is a technical and rebreather diving business.

Light blue colors

```html
<!DOCTYPE html>
<html lang="en">
<head>
<meta charset="utf-8">
<title>Crest Tide Store</title>
<link href="https://fonts.googleapis.com/css2?family=Arimo:ital,wght@0,400;0,700;1,400;1,700&display=swap" rel="stylesheet">
<style>
:root{
  --bar-top:#fcc23a;
  --bar-bottom:#e99a12;
  --sea-top:#1cb9e4;
  --sea-mid:#106a8d;
  --sea-deep:#0a3448;
  --tab:#3d9df0;
  --tab-active:#0f5fb8;
  --band-top:#f1f1f1;
  --band-bottom:#bdbdbd;
  --band-text:#3e3e3e;
  --side-col:rgba(38,56,64,.88);
  --center-col:#ffffff;
  --center-text:#2a2a2a;
  --card:#5a5a5a;
  --heading-blue:#1668b8;
  --link-blue:#2e86d8;
  --price:#b3151b;
  --white:#ffffff;
  --ink:#222;
  --phone:#1d3f50;
}
*{margin:0;padding:0;box-sizing:border-box}
html,body{width:1200px;height:1152px;overflow:hidden}
body{font-family:"Arimo",Arial,sans-serif;position:relative;color:var(--white)}
.sea{position:absolute;inset:0;background:radial-gradient(ellipse at 75% 15%,var(--sea-top) 0%,var(--sea-mid) 45%,var(--sea-deep) 100%)}
.abs{position:absolute}
.topbar{left:0;top:0;width:1200px;height:42px;background:linear-gradient(var(--bar-top),var(--bar-bottom));border-bottom:1px solid #b87708}
.topnav{left:98px;top:14px;font-size:13px;color:var(--ink);display:flex;gap:12px}
.shipping{left:531px;top:6px;width:131px;height:31px;border-radius:6px;background:linear-gradient(#fff7e4,#f0dcb0);color:#8a4b0a;font-weight:700;font-size:14px;display:flex;align-items:center;justify-content:center}
.search{left:727px;top:6px;width:363px;height:30px;border-radius:15px;background:linear-gradient(#525c63,#2f373c);overflow:hidden;border:1px solid #6d5a2a}
.search-btn{position:absolute;right:0;top:0;width:86px;height:100%;background:linear-gradient(#36a4f2,#1a7dd3);color:#0a2b4d;font-size:14px;display:flex;align-items:center;justify-content:center}
.brand{left:86px;top:62px;display:flex;align-items:center;gap:10px;font-size:34px;font-weight:700;color:var(--white)}
.brand-dot{width:26px;height:26px;border-radius:50%;background:var(--tab-active)}
.phone{right:112px;top:87px;font-size:18px;font-weight:700;color:var(--phone)}
.tab{top:117px;height:53px;width:157px;border-radius:10px 10px 0 0;background:var(--tab);display:flex;align-items:center;justify-content:center;font-size:15px;color:var(--white)}
.tab.active{background:var(--tab-active)}
.band{left:100px;top:170px;width:999px;height:42px;border-radius:10px 10px 0 0;background:linear-gradient(var(--band-top),var(--band-bottom));font-size:18px;font-weight:700;color:var(--band-text)}
.band span{position:absolute;top:12px}
.col{top:212px;height:761px}
.col-learn{left:100px;width:219px;background:var(--side-col)}
.col-shop{left:319px;width:547px;background:var(--center-col)}
.col-dive{left:866px;width:233px;background:var(--side-col)}
.video-card{left:108px;width:200px;height:173px;border-radius:12px;background:var(--card);border:1px solid #777}
.video-card h3{font-size:14px;text-align:center;margin-top:8px;color:#eee}
.video-card .thumb{position:absolute;left:4px;top:27px;width:190px;height:122px;background:linear-gradient(#dcdcdc,#9aa4a8)}
.video-card .watch{position:absolute;bottom:4px;width:100%;text-align:center;font-size:14px;font-weight:700;color:#eee}
.caption{left:114px;width:200px;font-size:12.5px;font-style:italic;line-height:21px}
.product-title{font-size:14.5px;color:var(--heading-blue)}
.product-img{width:176px;height:118px;background:linear-gradient(135deg,#f2f2f2,#9a9a9a);border:1px solid #ccc}
.product-text{width:176px;font-size:12.5px;font-style:italic;line-height:18px;text-align:justify;color:var(--center-text)}
.price-box{width:180px;height:37px;background:linear-gradient(#fff,#dedede);border:1px solid #bbb;box-shadow:0 1px 3px rgba(0,0,0,.25);display:flex;align-items:center;padding-left:12px;gap:34px}
.price{font-size:20px;color:var(--price)}
.shop-now{font-size:13px;color:#555;text-decoration:underline}
.dive-list{left:875px;top:244px;width:217px;display:flex;flex-direction:column}
.post{margin-bottom:8px}
.post-title{display:block;margin-left:2px;font-size:12px;font-style:italic;color:var(--link-blue);line-height:16px}
.post-text{margin-top:3px;font-size:12px;font-style:italic;line-height:18px;letter-spacing:-.1px;text-align:justify}
.more{margin:3px -7px 0 auto;width:56px;height:23px;border-radius:8px;background:linear-gradient(#fff,#d8d8d8);color:#222;font-size:12px;display:flex;align-items:center;justify-content:center}
.footer{left:0;width:1200px;top:997px;text-align:center;font-size:13px}
</style>
</head>
<body>
<div class="sea" role="img" aria-label="Underwater background photo of a rebreather diver above the sea floor"></div>

<header>
  <div class="abs topbar"></div>
  <nav class="abs topnav"><span>Home</span><span>|</span><span>About us</span><span>|</span><span>Send Email</span><span>|</span><span>Privacy Policy</span></nav>
  <div class="abs shipping">Free Shipping</div>
  <div class="abs search"><div class="search-btn">SEARCH</div></div>
  <div class="abs brand"><span class="brand-dot"></span>Crest Tide</div>
  <div class="abs phone">call us - 555.014.2280</div>
  <div class="abs tab active" style="left:607px">Best Seller</div>
  <div class="abs tab" style="left:769px">New Arrivals</div>
  <div class="abs tab" style="left:930px">Sales</div>
</header>

<div class="abs band"><span style="left:43px">learn</span><span style="left:241px">shop</span><span style="left:782px">dive</span></div>

<section class="abs col col-learn"></section>
<section class="abs col col-shop"></section>
<section class="abs col col-dive"></section>

<div class="abs video-card" style="top:232px"><h3>clearwave disinfectant</h3><div class="thumb" role="img" aria-label="Video still of a presenter showing a disinfectant product"></div><div class="watch">watch video</div></div>
<p class="abs caption" style="top:417px">Ut enim ad minim veniam, quis nos trud exercitation ullamco laboris</p>
<div class="abs video-card" style="top:475px"><h3>clearwave disinfectant</h3><div class="thumb" role="img" aria-label="Video still of a presenter showing a disinfectant product"></div><div class="watch">watch video</div></div>
<p class="abs caption" style="top:660px">Ut enim ad minim veniam, quis nos trud exercitation ullamco laboris</p>
<div class="abs video-card" style="top:706px"><h3>clearwave disinfectant</h3><div class="thumb" role="img" aria-label="Video still of a presenter showing a disinfectant product"></div><div class="watch">watch video</div></div>
<p class="abs caption" style="top:892px">Ut enim ad minim veniam, quis nos trud exercitation ullamco laboris</p>

<div class="abs product-title" style="left:369px;top:237px">BACK PALETTES WINGS</div>
<div class="abs product-img" style="left:369px;top:262px" role="img" aria-label="Back plate and wing harness product photo"></div>
<p class="abs product-text" style="left:369px;top:383px">Ut enim ad minim veniam, quis nos trud exercitation ullamco laboris</p>
<div class="abs price-box" style="left:364px;top:442px"><span class="price">$500</span><span class="shop-now">Shop Now</span></div>

<div class="abs product-title" style="left:591px;top:237px">LIGHTS</div>
<div class="abs product-img" style="left:591px;top:262px" role="img" aria-label="Dive torches and canister light product photo"></div>
<p class="abs product-text" style="left:591px;top:383px">Ut enim ad minim veniam, quis nos trud exercitation ullamco laboris</p>
<div class="abs price-box" style="left:586px;top:442px"><span class="price">$500</span><span class="shop-now">Shop Now</span></div>

<div class="abs product-title" style="left:361px;top:517px">TANKS</div>
<div class="abs product-img" style="left:361px;top:543px" role="img" aria-label="Diving cylinders product photo"></div>
<p class="abs product-text" style="left:361px;top:664px">Ut enim ad minim veniam, quis nos trud exercitation ullamco laboris</p>
<div class="abs price-box" style="left:356px;top:722px"><span class="price">$500</span><span class="shop-now">Shop Now</span></div>

<div class="abs product-title" style="left:594px;top:521px">HARDWARE</div>
<div class="abs product-img" style="left:594px;top:546px" role="img" aria-label="Stainless hardware, clips and o-rings product photo"></div>
<p class="abs product-text" style="left:594px;top:667px">Ut enim ad minim veniam, quis nos trud exercitation ullamco laboris</p>
<div class="abs price-box" style="left:590px;top:727px"><span class="price">$500</span><span class="shop-now">Shop Now</span></div>

<div class="abs dive-list">
  <article class="post">
    <span class="post-title">deepwater expo 2012</span>
    <p class="post-text">Lorem ipsum dolor sit amet, consectetur adipisicing elit, sed do eiusmod tempor incididunt ut labore et dolore magna aliqua. Ut enim ad minim veniam, quis nostrud exercitation</p>
    <div class="more">More</div>
  </article>
  <article class="post">
    <span class="post-title">Truk Lagoon CCR Trip</span>
    <p class="post-text">Lorem ipsum dolor sit amet, consectetur adipisicing elit, sed do eiusmod tempor incididunt ut labore et dolore magna aliqua. Ut enim ad minim veniam, quis nostrud exercitation ullamco laboris</p>
    <div class="more">More</div>
  </article>
  <article class="post">
    <span class="post-title">Dive With Team</span>
    <p class="post-text">Lorem ipsum dolor sit amet, consectetur adipisicing elit, sed do eiusmod tempor incididunt ut labore et dolore magna aliqua. Ut enim ad</p>
    <div class="more">More</div>
  </article>
  <article class="post">
    <span class="post-title">Crest Tide</span>
    <p class="post-text">Lorem ipsum dolor sit amet, consectetur adipisicing elit, sed do eiusmod tempor incididunt ut labore et dolore magna aliqua. Ut enim ad minim veniam, quis nostrud exercitation ullamco laboris nisi ut aliquip ex,</p>
    <div class="more">More</div>
  </article>
</div>

<footer class="abs footer">© All Right Reserved 2012 | Privacy Policy | Terms &amp; Conditions</footer>
</body>
</html>
```